KRV Business Card

Looking for a business card for my restaurant group I own. Four different concepts:

Copperfield Alehouse
Bristow Alehouse
Tanager's Stone Hearth Kitchen
Pellston Patty Company

Card doesn't need to include all the logos.

```html
<!DOCTYPE html>
<html lang="en">
<head>
<meta charset="utf-8">
<title>KRV Business Card</title>
<link href="https://fonts.googleapis.com/css2?family=Noto+Sans:wght@400;600&display=swap" rel="stylesheet">
<style>
  :root {
    --page: #ebebeb;
    --card: #1b1a1b;
    --gold: #c9b06c;
    --ink: #ffffff;
    --ghost: #232223;
  }
  * { margin: 0; padding: 0; box-sizing: border-box; }
  html, body {
    width: 1200px; height: 800px; overflow: hidden;
    background: var(--page);
    font-family: "Noto Sans", sans-serif;
  }
  .card {
    position: absolute; left: 315px;
    width: 570px; height: 330px;
    background: var(--card);
    overflow: hidden;
  }
  .card--front { top: 50px; }
  .card--back { top: 419px; }

  .ghost-mark {
    position: absolute; left: 56px; top: 92px;
    font-size: 150px; font-weight: 600; line-height: 1;
    letter-spacing: 4px;
    color: var(--ghost);
  }
  .holder {
    position: absolute; right: 298px; top: 150px;
    font-size: 19px; font-weight: 600; color: var(--gold);
    line-height: 26px; white-space: nowrap;
  }
  .divider {
    position: absolute; left: 285px; top: 151px;
    width: 1px; height: 28px; background: var(--gold);
  }
  .contact {
    position: absolute; left: 298px; top: 143px;
    list-style: none;
  }
  .contact li {
    display: flex; align-items: center;
    height: 21px; font-size: 15px; color: var(--ink);
  }
  .contact svg { width: 10px; height: 10px; margin-right: 9px; fill: var(--gold); }
  .company-line {
    position: absolute; left: 0; right: 0; top: 281px;
    text-align: center; font-size: 14.5px; color: var(--ink);
  }

  .brand {
    position: absolute; left: 0; right: 0; top: 92px;
    text-align: center; color: var(--gold); font-weight: 600;
  }
  .brand__initials { display: block; font-size: 62px; line-height: 70px; letter-spacing: 4px; }
  .brand__name { display: block; font-size: 20px; line-height: 40px; letter-spacing: 4px; text-transform: uppercase; }
</style>
</head>
<body>
  <section class="card card--front">
    <div class="ghost-mark" aria-hidden="true">KRV</div>
    <p class="holder">Dana Holloway</p>
    <span class="divider"></span>
    <ul class="contact">
      <li>
        <svg viewBox="0 0 10 10" aria-hidden="true"><path d="M2 0.5 L3.6 2.6 L2.7 3.6 Q3.8 5.9 6.3 7.2 L7.3 6.3 L9.5 7.9 L8.4 9.5 Q3.6 9 0.5 1.6 Z"/></svg>
        555-014-2290
      </li>
      <li>
        <svg viewBox="0 0 10 10" aria-hidden="true"><path d="M0.5 2 H9.5 V8.5 H0.5 Z M1.5 3 L5 5.6 L8.5 3 V2.8 H1.5 Z" fill-rule="evenodd"/></svg>
        dana@krvrestaurants.com
      </li>
    </ul>
    <p class="company-line">Kestrel Ridge Ventures</p>
  </section>

  <section class="card card--back">
    <div class="brand">
      <span class="brand__initials">KRV</span>
      <span class="brand__name">Kestrel Ridge Ventures</span>
    </div>
  </section>
</body>
</html>
```